BOLD & MINIMALIST DESIGN NEEDED

We want a very bold but minimalistic business card design that is impactful and utilizes both sides of the business card. Our current logo is included for your use.

We want bold fonts and good use of negative space. We don't want the logo to overpower the design.

Target Market(s)

Professionals who are building new commercial buildings.

Industry/Entity Type

Construction

Contact Information for Business Card

Name, Title, email, office phone, cell phone, website

Font styles to use
Serif
Sans Serif

Requirements
Must have
• Bold design!

```html
<!DOCTYPE html>
<html lang="en">
<head>
<meta charset="utf-8">
<title>Ridgeline Design + Build — Business Card</title>
<link href="https://fonts.googleapis.com/css2?family=Montserrat:wght@400;700;800&display=swap" rel="stylesheet">
<style>
  :root {
    --backdrop: #dcdcdc;
    --ink: #0d0e10;
    --paper: #ffffff;
    --green: #78c043;
  }
  * { margin: 0; padding: 0; box-sizing: border-box; }
  html, body { width: 1200px; height: 1200px; overflow: hidden; }
  body {
    background: var(--backdrop);
    position: relative;
    font-family: "Montserrat", Arial, sans-serif;
  }
  .card {
    position: absolute;
    left: 179px;
    width: 861px;
    height: 496px;
  }
  .card-front {
    top: 84px;
    background: var(--ink);
    display: flex;
    flex-direction: column;
    align-items: center;
    justify-content: center;
    color: var(--paper);
  }
  .brand-square {
    width: 46px;
    height: 46px;
    background: var(--green);
    margin-bottom: 26px;
  }
  .brand-name {
    font-weight: 800;
    text-align: center;
    line-height: 1;
  }
  .brand-name .word { display: block; font-size: 54px; letter-spacing: 1px; }
  .brand-name .sub { display: block; font-size: 20px; letter-spacing: 7px; margin-top: 10px; }

  .card-back {
    top: 622px;
    background: var(--paper);
    color: var(--ink);
    overflow: hidden;
  }
  .card-back .brand-name {
    position: absolute;
    left: 35px;
    top: 38px;
    text-align: left;
    color: var(--ink);
  }
  .card-back .brand-name .word { font-size: 56px; }
  .card-back .brand-name .sub { font-size: 21px; letter-spacing: 8px; margin-top: 12px; padding-left: 4px; }

  .person { position: absolute; left: 33px; top: 196px; }
  .person-name { font-weight: 800; font-size: 35px; line-height: 1.1; }
  .person-title { font-weight: 700; font-size: 28px; color: var(--green); line-height: 1.2; }

  .contact-list {
    position: absolute;
    left: 34px;
    top: 338px;
    list-style: none;
  }
  .contact-list li {
    display: flex;
    align-items: center;
    height: 35px;
    font-size: 23px;
    letter-spacing: 0.8px;
  }
  .contact-list svg { width: 24px; height: 24px; margin-right: 14px; fill: var(--ink); flex: none; }

  .accent-block {
    position: absolute;
    right: 36px;
    bottom: 0;
    width: 200px;
    height: 200px;
    background: linear-gradient(160deg, #d8edc4 0%, var(--green) 70%);
  }
</style>
</head>
<body>
  <section class="card card-front">
    <div class="brand-square"></div>
    <div class="brand-name">
      <span class="word">RIDGELINE</span>
      <span class="sub">DESIGN + BUILD</span>
    </div>
  </section>

  <section class="card card-back">
    <div class="brand-name">
      <span class="word">RIDGELINE</span>
      <span class="sub">DESIGN + BUILD</span>
    </div>

    <div class="person">
      <p class="person-name">Name Surename</p>
      <p class="person-title">Director</p>
    </div>

    <ul class="contact-list">
      <li>
        <svg viewBox="0 0 24 24" aria-hidden="true"><path d="M6.6 10.8a15.1 15.1 0 0 0 6.6 6.6l2.2-2.2c.3-.3.7-.4 1-.2 1.1.4 2.3.6 3.6.6.6 0 1 .4 1 1V20c0 .6-.4 1-1 1A17 17 0 0 1 3 4c0-.6.4-1 1-1h3.5c.6 0 1 .4 1 1 0 1.3.2 2.5.6 3.6.1.3 0 .7-.2 1z"/></svg>
        555-014-2200
      </li>
      <li>
        <svg viewBox="0 0 24 24" aria-hidden="true"><path d="M2 8c0-2 4-4 10-4s10 2 10 4v2h-5V8H7v2H2z M6 11h12l3 9H3z"/></svg>
        555-014-2200
      </li>
      <li>
        <svg viewBox="0 0 24 24" aria-hidden="true"><path d="M2 5h20v14H2z M4 7v.5l8 6 8-6V7z M4 10v7h16v-7l-8 6z" fill-rule="evenodd"/></svg>
        info@rdb-build.com
      </li>
      <li>
        <svg viewBox="0 0 24 24" aria-hidden="true"><path d="M12 2a10 10 0 1 0 0 20 10 10 0 0 0 0-20zm0 2c.9 0 2.2 2 2.7 5H9.3c.5-3 1.8-5 2.7-5zm-2.9.6C8.3 6 7.6 7.4 7.3 9H4.8a8 8 0 0 1 4.3-4.4zm5.8 0A8 8 0 0 1 19.2 9h-2.5c-.3-1.6-1-3-1.8-4.4zM4.3 11h2.9v2H4.3a8 8 0 0 1 0-2zm4.9 0h5.6v2H9.2zm7.6 0h2.9a8 8 0 0 1 0 2h-2.9zM4.8 15h2.5c.3 1.6 1 3 1.8 4.4A8 8 0 0 1 4.8 15zm4.5 0h5.4c-.5 3-1.8 5-2.7 5s-2.2-2-2.7-5zm7.4 0h2.5a8 8 0 0 1-4.3 4.4c.8-1.4 1.5-2.8 1.8-4.4z"/></svg>
        www.rdb-build.com
      </li>
    </ul>

    <div class="accent-block"></div>
  </section>
</body>
</html>
```